Construction Company

Design a clutter free business card, it can be double-sided utilizing the logo for VKM Ltd simple with all relevant contact information.

Please also a letterhead design to function for the purposes of invoicing, all mail requirements, with header to be distinctive while the footer ties page together and incorporates all necessary information.

For now, please use generic / dummy text and when a winner is selected, I will disclose the contact information.

Hi Designers! Please read the updated brief which includes the design of a business card and letterhead. Thank you!

```html
<!DOCTYPE html>
<html lang="en">
<head>
<meta charset="UTF-8">
<title>VKM Ltd Business Card</title>
<link rel="stylesheet" href="https://fonts.googleapis.com/css2?family=Libre+Baskerville:wght@400;700&family=Arimo:wght@400&display=swap">
<style>
  :root {
    --bg: #1c1c1d;
    --card: #0c0c0c;
    --card-edge: #1a1a1a;
    --brand-blue: #1b3fb0;
    --gold: #d9a31c;
    --text-light: #d8d8d8;
    --divider: #2e2e2e;
    --silver: #e4e4e4;
  }
  * { margin: 0; padding: 0; box-sizing: border-box; }
  html, body {
    width: 1200px; height: 900px; overflow: hidden;
    background: var(--bg);
  }
  .canvas {
    position: relative; width: 1200px; height: 900px;
    display: flex; align-items: center; justify-content: center; gap: 60px;
  }
  .card {
    position: relative; width: 510px; height: 292px;
    background: var(--card);
    border: 1px solid var(--card-edge);
    border-radius: 20px;
    box-shadow: 0 18px 40px rgba(0,0,0,.55);
  }
  .wordmark {
    font-family: "Libre Baskerville", serif;
    font-weight: 700;
    white-space: nowrap;
  }
  /* front side */
  .card-front .wordmark {
    position: absolute; left: 44px; top: 128px;
    font-size: 40px; color: var(--brand-blue);
  }
  .card-front .divider {
    position: absolute; left: 262px; top: 48px; width: 1px; height: 196px;
    background: var(--divider);
  }
  .contact {
    position: absolute; left: 290px; top: 52px;
    font-family: "Arimo", sans-serif; color: var(--text-light);
  }
  .contact-name {
    font-family: "Libre Baskerville", serif; font-weight: 700;
    font-size: 15px; color: var(--gold); letter-spacing: .5px;
  }
  .contact-role { font-size: 13px; margin: 2px 0 16px; }
  .contact-list { list-style: none; font-size: 13px; line-height: 19px; }
  .contact-list li { display: flex; align-items: center; gap: 8px; }
  .contact-list svg { width: 12px; height: 12px; flex: none; }
  .contact-address { font-size: 13px; line-height: 18px; margin-top: 14px; padding-left: 20px; }
  /* back side */
  .card-back { display: flex; align-items: center; justify-content: center; }
  .card-back .wordmark { font-size: 48px; color: var(--silver); }
</style>
</head>
<body>
<main class="canvas">
  <section class="card card-front" aria-label="Business card front">
    <div class="wordmark">VKM Ltd</div>
    <div class="divider"></div>
    <div class="contact">
      <p class="contact-name">DANIEL HART</p>
      <p class="contact-role">Managing Director</p>
      <ul class="contact-list">
        <li>
          <svg viewBox="0 0 12 12" aria-hidden="true"><path d="M2.5 1l2 2.2-1 1.2c.7 1.5 1.8 2.6 3.2 3.2l1.2-1L10 8.6 8.8 10.5C5 10 2 7 1.5 3.2z" fill="var(--gold)"/></svg>
          044-555 010 200
        </li>
        <li>
          <svg viewBox="0 0 12 12" aria-hidden="true"><rect x="3" y="1" width="6" height="10" rx="1" fill="none" stroke="var(--gold)" stroke-width="1.3"/><circle cx="6" cy="9" r=".7" fill="var(--gold)"/></svg>
          044-555 010 300
        </li>
        <li>
          <svg viewBox="0 0 12 12" aria-hidden="true"><rect x="1" y="2.5" width="10" height="7" fill="var(--gold)"/><path d="M1 2.5l5 4 5-4" fill="none" stroke="var(--card)" stroke-width="1"/></svg>
          info@vkmbuild.com
        </li>
        <li>
          <svg viewBox="0 0 12 12" aria-hidden="true"><circle cx="6" cy="6" r="5" fill="none" stroke="var(--gold)" stroke-width="1.2"/><path d="M1 6h10M6 1c-2.5 3-2.5 7 0 10M6 1c2.5 3 2.5 7 0 10" fill="none" stroke="var(--gold)" stroke-width=".9"/></svg>
          www.vkmbuild.com
        </li>
      </ul>
      <p class="contact-address">421, Address line goes here<br>45452, Country Name</p>
    </div>
  </section>

  <section class="card card-back" aria-label="Business card back">
    <div class="wordmark">VKM Ltd</div>
  </section>
</main>
</body>
</html>
```